Website for Life Strategies business

We need a website to present our video, audio and print content to subcribers at Bright Summit Mentors. We will offer a team of coaches who can help people breakthrough the barriers that keep them from reaching their physical, spiritual, financial, leadership and relationship goals.

Target Market(s)

Anyone who needs help with strategies to take their life to a new level of success.

Industry/Entity Type

Life Coaching

Logo Text

Bright Summit Mentors

Number of Pages Required

5+ page

Colors

Designer to choose colors to be used in the design.

Requirements
Must have
• The ability to present content as a package that includes Word Documents, videos and audio content as well as to be able to display books for sale. Each week their would be a new package for subscribers to access. It should provide the ability for subscribers to comment on the material and share how their lives were changed by the content. Should also include a shop page to offer merchandise for sale.
Nice to have
• Not sure
Should not have
• Not sure

```html
<!DOCTYPE html>
<html lang="en">
<head>
<meta charset="utf-8">
<title>Bright Summit Mentors</title>
<link href="https://fonts.googleapis.com/css2?family=Roboto:wght@400;500;700&family=Open+Sans:wght@400;600;700&display=swap" rel="stylesheet">
<style>
:root{
  --teal:#0f7b89;
  --teal-dark:#0b5f6b;
  --red:#e2242b;
  --red-soft:#b8404c;
  --text:#333;
  --muted:#555;
  --white:#fff;
}
*{box-sizing:border-box;margin:0;padding:0}
html,body{width:1200px;height:3169px;overflow:hidden}
body{font-family:'Roboto',sans-serif;color:var(--text);background:var(--white);position:relative}
a{color:inherit;text-decoration:none}

.topbar{position:absolute;left:0;top:0;width:1200px;height:38px;background:var(--teal);color:var(--white);font-size:14px;font-weight:500}
.topbar .phone{position:absolute;left:99px;top:10px;display:flex;align-items:center;gap:8px}
.topbar .links{position:absolute;right:99px;top:10px}
.topbar .links span{margin:0 10px}

.header{position:absolute;left:0;top:38px;width:1200px;height:137px;background:var(--white)}
.brand{position:absolute;left:99px;top:36px;display:flex;align-items:center;gap:14px}
.brand .dot{width:64px;height:64px;border-radius:50%;background:var(--red)}
.brand .name{font-weight:700;font-size:26px;line-height:30px;color:var(--teal);text-transform:uppercase}
.search{position:absolute;left:733px;top:32px;width:366px;height:36px;border:1px solid #999;border-radius:3px;font-size:13px;color:#444;padding:9px 12px}
.search .btn{position:absolute;right:3px;top:3px;width:28px;height:28px;background:var(--red);border-radius:3px}
.nav{position:absolute;right:99px;top:102px;display:flex;gap:40px;font-size:15px;font-weight:500;color:#222}
.nav .active{color:var(--red);position:relative}
.nav .active::after{content:"";position:absolute;left:-8px;right:-8px;bottom:-12px;height:3px;background:var(--red)}

.hero{position:absolute;left:0;top:175px;width:1200px;height:543px;background:linear-gradient(100deg,#cfc6bc 0%,#e6ddd2 35%,#f1ebe3 60%,#d8d2c8 100%)}
.hero .title{position:absolute;left:99px;top:106px;width:581px;height:74px;background:rgba(226,36,43,.88);color:var(--white);font-family:'Open Sans',sans-serif;font-weight:700;font-size:38px;line-height:74px;padding-left:16px}
.hero .lead{position:absolute;left:99px;top:210px;width:520px;font-size:16px;line-height:28px;color:var(--white);text-shadow:0 1px 2px rgba(0,0,0,.4)}
.btn-teal{position:absolute;display:block;background:var(--teal);color:var(--white);border:2px solid var(--white);font-size:16px;font-weight:500;text-align:center}
.hero .btn-teal{left:99px;top:307px;width:125px;height:48px;line-height:44px}
.hero .wave{position:absolute;left:0;bottom:0;width:1200px;height:110px}

.welcome{position:absolute;left:0;top:718px;width:1200px;text-align:center}
.heading{font-weight:700;color:var(--red);font-size:28px}
.rule{width:160px;height:2px;background:var(--red);margin:0 auto}
.welcome .heading{position:absolute;left:0;right:0;top:78px}
.welcome .rule{position:absolute;left:520px;top:138px}
.welcome p{position:absolute;left:127px;top:182px;width:946px;font-size:13px;line-height:27px;color:var(--text)}
.divider{position:absolute;left:99px;top:1041px;width:1002px;height:2px;background:var(--teal)}

.services{position:absolute;left:0;top:1043px;width:1200px;height:546px}
.services .heading{position:absolute;left:0;right:0;top:50px;text-align:center}
.services .rule{position:absolute;left:550px;top:106px;width:100px}
.service{position:absolute;top:172px;width:330px;text-align:center}
.service .icon{width:158px;height:158px;margin:0 auto;border-radius:50%;border:3px solid var(--teal);padding:6px}
.service .icon span{display:block;width:100%;height:100%;border-radius:50%;background:var(--teal)}
.service.red .icon{border-color:var(--red)}
.service.red .icon span{background:var(--red)}
.service h3{margin-top:42px;font-size:21px;font-weight:500;color:var(--teal)}
.service.red h3{color:var(--red)}
.service p{margin-top:14px;font-size:13px;line-height:27px;color:var(--muted);padding:0 20px}

.coaches{position:absolute;left:0;top:1589px;width:1200px;height:530px;background:linear-gradient(90deg,#0f7b89 0%,#17808d 50%,#0e6f7c 100%);color:var(--white)}
.coaches h2{position:absolute;left:99px;top:74px;width:640px;font-size:27px;line-height:40px;font-weight:700}
.coaches p{position:absolute;left:99px;width:616px;font-size:13px;line-height:25px}
.coaches .p1{top:170px}
.coaches .p2{top:290px}
.coaches .btn-teal{left:99px;top:397px;width:122px;height:48px;line-height:44px;background:transparent;font-size:15px}
.finder{position:absolute;left:761px;top:65px;width:338px;height:400px;background:rgba(6,60,70,.75);border:2px solid #cfe3e6;border-radius:3px;overflow:hidden}
.finder .head{position:relative;height:120px;color:var(--white);text-align:center;font-size:21px;font-weight:700;line-height:34px;padding-top:18px}
.finder .head svg{position:absolute;left:0;top:0;width:334px;height:120px;z-index:0}
.finder .head span{position:relative;z-index:1}
.field{position:absolute;left:0;width:334px;font-size:14px;line-height:24px}
.field label{position:absolute;left:22px;width:90px;text-align:center}
.field .box{position:absolute;left:117px;width:202px;height:38px;border:2px solid #e6eff0;border-radius:6px;font-size:12px;padding:9px 8px}
.f1{top:150px}.f1 label{top:0}.f1 .box{top:6px}
.f2{top:218px}.f2 label{top:0}.f2 .box{top:0}.f2 .box2{top:52px}
.finder .go{position:absolute;left:117px;top:320px;width:108px;height:38px;background:var(--red);border:1px solid #f4c6c8;border-radius:2px;font-size:14px;font-weight:500;text-align:center;line-height:36px}

.media{position:absolute;left:0;top:2119px;width:1200px;height:676px}
.media .heading{position:absolute;left:0;right:0;top:62px;text-align:center}
.media .rule{position:absolute;left:550px;top:116px;width:100px}
.card{position:absolute;top:167px;width:319px;text-align:center}
.card .thumb{position:relative;height:235px;border:2px solid var(--teal);padding:3px}
.card.red .thumb{border-color:var(--red)}
.card .thumb span{display:block;width:100%;height:100%}
.card .thumb svg{position:absolute;left:50%;top:50%;width:56px;height:56px;margin:-28px 0 0 -28px}
.card p{margin-top:30px;font-size:16px;font-weight:500;line-height:23px;color:var(--teal);padding:0 20px}
.card.red p{color:var(--red)}
.btn-red{position:absolute;left:452px;top:539px;width:296px;height:55px;background:var(--red);color:var(--white);border-radius:3px;font-size:16px;font-weight:500;text-align:center;line-height:55px}

.footer{position:absolute;left:0;top:2795px;width:1200px;height:374px;background:var(--teal);color:var(--white)}
.footer .brand{left:441px;top:68px}
.footer .brand .dot{background:var(--white)}
.footer .brand .name{color:var(--white);font-size:29px;line-height:34px}
.footer nav{position:absolute;left:0;right:0;top:218px;text-align:center;font-size:17px;font-weight:500}
.footer nav span.sep{margin:0 30px}
.footer .line{position:absolute;left:99px;top:285px;width:1002px;height:2px;background:rgba(255,255,255,.8)}
.footer .copy{position:absolute;left:99px;top:320px;font-size:13px}
.footer .social{position:absolute;left:950px;top:312px;display:flex;gap:8px}
.footer .social span{width:32px;height:32px;border:2px solid var(--white);border-radius:50%}
</style>
</head>
<body>

<div class="topbar">
  <div class="phone">
    <svg width="14" height="14" viewBox="0 0 24 24" aria-hidden="true"><path fill="#fff" d="M6.6 10.8a15 15 0 0 0 6.6 6.6l2.2-2.2a1 1 0 0 1 1-.25 11.4 11.4 0 0 0 3.6.57 1 1 0 0 1 1 1V20a1 1 0 0 1-1 1A17 17 0 0 1 3 4a1 1 0 0 1 1-1h3.5a1 1 0 0 1 1 1c0 1.25.2 2.45.57 3.57a1 1 0 0 1-.25 1z"/></svg>
    180 555 0142
  </div>
  <div class="links">Join Our Program<span>|</span>Counselling<span>|</span>Lifestyle Strategy</div>
</div>

<header class="header">
  <div class="brand"><span class="dot"></span><div class="name">Bright Summit<br>Mentors</div></div>
  <div class="search">Search<span class="btn"></span></div>
  <nav class="nav">
    <a class="active">HOME</a><a>ABOUT US</a><a>COUNSELLING</a><a>BLOG</a><a>VIDEOS</a><a>CONTACT</a>
  </nav>
</header>

<section class="hero" role="img" aria-label="Smiling couple sitting together in a bright living room">
  <div class="title">BRIGHT SUMMIT MENTORS</div>
  <p class="lead">We will offer a team of coaches who can help people breakthrough the barriers that keep them from reaching their physical</p>
  <a class="btn-teal">Read More</a>
  <svg class="wave" viewBox="0 0 1200 110" preserveAspectRatio="none" aria-hidden="true">
    <path d="M0 66 C300 95 520 120 700 104 C900 86 1050 50 1200 26 L1200 110 L0 110Z" fill="#fff"/>
    <path d="M0 66 C300 95 520 120 700 104 C900 86 1050 50 1200 26" fill="none" stroke="#0f7b89" stroke-width="4"/>
  </svg>
</section>

<section class="welcome">
  <h2 class="heading">WELCOME TO BRIGHT SUMMIT MENTORS</h2>
  <div class="rule"></div>
  <p>Nemo enim ipsam voluptatem quia voluptas sit aspernatur aut odit aut fugit, sed quia consequuntur magni dolores eos qui ratione voluptatem sequi nesciunt. Neque porro quisquam est, qui dolorem ipsum quia dolor sit amet, consectetur, adipisci velit, sed quia non numquam eius modi tempora incidunt ut labore et dolore magnam aliquam quaerat voluptatem. Ut enim ad minima veniam, quis nostrum exercitationem ullam corporis suscipit laboriosam, nisi ut aliquid ex ea commodi consequatur.</p>
</section>
<div class="divider"></div>

<section class="services">
  <h2 class="heading">Our Services</h2>
  <div class="rule"></div>
  <div class="service" style="left:89px">
    <div class="icon" role="img" aria-label="Team leadership icon"><span></span></div>
    <h3>Physical Leadership</h3>
    <p>Sed ut perspiciatis unde omnis iste natus error sit voluptatem accusantium doloremque laudantium totam rem aperiam.</p>
  </div>
  <div class="service red" style="left:435px">
    <div class="icon" role="img" aria-label="Heart in speech bubble icon"><span></span></div>
    <h3>Relationship Goals</h3>
    <p>Sed ut perspiciatis unde omnis iste natus error sit voluptatem accusantium doloremque laudantium totam rem aperiam.</p>
  </div>
  <div class="service" style="left:779px">
    <div class="icon" role="img" aria-label="Financial meeting icon"><span></span></div>
    <h3>Financial Leadership</h3>
    <p>Sed ut perspiciatis unde omnis iste natus error sit voluptatem accusantium doloremque laudantium totam rem aperiam.</p>
  </div>
</section>

<section class="coaches">
  <h2>We will offer a team of coaches who can help people breakthrough the barriers</h2>
  <p class="p1">Nemo enim ipsam voluptatem quia voluptas sit aspernatur aut odit aut fugit, sed quia consequuntur magni dolores eos qui ratione voluptatem sequi nesciunt. Neque porro quisquam est, qui dolorem ipsum quia dolor sit amet, consectetur, adipisci velit, sed quia non numquam eius modi tempora incidunt ut labore et dolore magnam aliquam quaerat voluptatem.</p>
  <p class="p2">Enim ad minima veniam, quis nostrum exercitationem ullam corporis suscipit laboriosam, nisi ut aliquid ex ea commodi consequatur autem vel eum iure reprehenderit qui in ea voluptate velit esse quam commodi consequatur.</p>
  <a class="btn-teal">Read More</a>

  <form class="finder">
    <div class="head">
      <svg viewBox="0 0 334 120" preserveAspectRatio="none" aria-hidden="true"><path d="M0 0H334V92C240 122 94 122 0 92Z" fill="#b8404c"/></svg>
      <span>Find Our Specialists<br>Near You</span>
    </div>
    <div class="field f1"><label>Type of Counselling</label><div class="box">Select</div></div>
    <div class="field f2"><label>Location<br>(or)<br>Postcode</label><div class="box"></div><div class="box box2"></div></div>
    <div class="go">Search</div>
  </form>
</section>

<section class="media">
  <h2 class="heading">Our Video &amp; Audio</h2>
  <div class="rule"></div>
  <div class="card" style="left:99px">
    <div class="thumb"><span role="img" aria-label="Coach talking with a client" style="background:linear-gradient(120deg,#8a6a55,#d9b48a 55,#5f5048)"></span><svg viewBox="0 0 56 56" aria-hidden="true"><circle cx="28" cy="28" r="25" fill="rgba(0,0,0,.25)" stroke="#fff" stroke-width="3"/><path d="M22 17 40 28 22 39Z" fill="#fff"/></svg></div>
    <p>Nemo enim ipsam voluptatem quia voluptas sit aspernatur</p>
  </div>
  <div class="card red" style="left:441px">
    <div class="thumb"><span role="img" aria-label="Smiling woman in a counselling session" style="background:linear-gradient(120deg,#9fa63a,#c8c08a 50%,#4c6a8c)"></span><svg viewBox="0 0 56 56" aria-hidden="true"><circle cx="28" cy="28" r="25" fill="rgba(0,0,0,.25)" stroke="#fff" stroke-width="3"/><path d="M22 17 40 28 22 39Z" fill="#fff"/></svg></div>
    <p>Sed ut perspiciatis unde omnis iste natus error sit voluptatem</p>
  </div>
  <div class="card" style="left:782px">
    <div class="thumb"><span role="img" aria-label="Counsellor taking notes with a client" style="background:linear-gradient(120deg,#7b7f82,#c9c6c0 50%,#8f8f8f)"></span><svg viewBox="0 0 56 56" aria-hidden="true"><circle cx="28" cy="28" r="25" fill="rgba(0,0,0,.25)" stroke="#fff" stroke-width="3"/><path d="M22 17 40 28 22 39Z" fill="#fff"/></svg></div>
    <p>Accusantium doloremque laudantium, totam rem aperiam</p>
  </div>
  <a class="btn-red">AUDIO AND PRINT CONTENT</a>
</section>

<footer class="footer">
  <div class="brand"><span class="dot"></span><div class="name">Bright Summit<br>Mentors</div></div>
  <nav>HOME<span class="sep">|</span>ABOUT US<span class="sep">|</span>COUNSELLING<span class="sep">|</span>BLOG<span class="sep">|</span>VIDEOS<span class="sep">|</span>CONTACT</nav>
  <div class="line"></div>
  <div class="copy">Copyright © 2017 Bright Summit Mentors. All Right Reserved</div>
  <div class="social" aria-label="Social links"><span></span><span></span><span></span><span></span></div>
</footer>

</body>
</html>
```